Velvet Pressings Techno Label Business Card

I'm looking for a very clean business card for my Velvet Pressings music label. The label focusses on techno music. The card should include:

• my name : Tomas Brandt as "Founder & CEO"
• email address: tomas@velvet-pressings.example
• web: www.velvet-pressings.example
• facebook logo + /velvetpress
• twitter logo + /velvetpress
• soundcloud logo + /velvetpressings

Feel free to include your ideas! I'm looking forward to discuss about it.

Tomas

Industry/Entity Type

Business

Contact Information for Business Card

I don't like glossy cards. Prefer matt.

Requirements
Nice to have
• Maybe on one side the complete logo, other side just the icon.
Should not have
• Flashy stuff. Must be clean and business like style.

```html
<!DOCTYPE html>
<html lang="en">
<head>
<meta charset="utf-8">
<title>Velvet Pressings – Business Card</title>
<link rel="stylesheet" href="https://fonts.googleapis.com/css2?family=Arimo:wght@700&family=Didact+Gothic&display=swap">
<style>
  :root {
    --orange: #ff6a0d;
    --grey: #8c8c8c;
    --grey-band: #9a9a9a;
    --grey-dark: #4a4a4a;
    --card: #ffffff;
    --backdrop: #e9e9e7;
  }
  html, body {
    margin: 0;
    width: 1200px;
    height: 900px;
    overflow: hidden;
    background: var(--backdrop);
  }
  .canvas {
    position: relative;
    width: 1200px;
    height: 900px;
  }
  .card {
    position: absolute;
    left: 150px;
    top: 180px;
    width: 900px;
    height: 540px;
    background: var(--card);
    border-radius: 38px;
    overflow: hidden;
    box-shadow: 0 2px 6px rgba(0,0,0,0.12);
  }
  .card__swoosh {
    position: absolute;
    inset: 0;
  }
  .brand {
    position: absolute;
    left: 0;
    width: 100%;
    top: 48px;
    text-align: center;
  }
  .brand__dot {
    display: block;
    width: 46px;
    height: 46px;
    margin: 0 0 8px 505px;
    border: 10px solid var(--orange);
    border-radius: 50%;
  }
  .brand__name {
    margin: 0;
    font-family: "Arimo", Arial, sans-serif;
    font-weight: 700;
    font-size: 46px;
    line-height: 52px;
    letter-spacing: -1px;
    color: var(--orange);
    padding-left: 60px;
  }
  .contact {
    position: absolute;
    top: 206px;
    left: 0;
    width: 100%;
    font-family: "Didact Gothic", "Century Gothic", sans-serif;
    font-variant: small-caps;
    letter-spacing: 2.5px;
    font-size: 20px;
    color: var(--grey-dark);
  }
  .contact__person {
    position: absolute;
    right: 448px;
    top: 2px;
    text-align: right;
    line-height: 27px;
  }
  .contact__name { color: var(--orange); }
  .contact__address { margin-top: 14px; }
  .contact__divider {
    position: absolute;
    left: 470px;
    top: 0;
    width: 1.5px;
    height: 150px;
    background: var(--grey);
  }
  .contact__lines {
    position: absolute;
    left: 490px;
    top: 2px;
    margin: 0;
    padding: 0;
    list-style: none;
    line-height: 27px;
  }
  .contact__lines li {
    display: flex;
    align-items: center;
    gap: 10px;
  }
  .contact__lines li.gap { margin-top: 8px; }
  .icon {
    width: 18px;
    height: 18px;
    flex: none;
  }
</style>
</head>
<body>
<main class="canvas">
  <section class="card" aria-label="Velvet Pressings business card">
    <svg class="card__swoosh" viewBox="0 0 900 540" preserveAspectRatio="none" aria-hidden="true">
      <path d="M0,378 C180,430 470,468 890,500 C470,486 170,452 0,406 Z" fill="var(--grey-band)"/>
      <path d="M0,418 C180,470 480,500 900,516 L900,540 L0,540 Z" fill="var(--orange)"/>
    </svg>

    <header class="brand">
      <span class="brand__dot" aria-hidden="true"></span>
      <h1 class="brand__name">Velvet Pressings</h1>
    </header>

    <div class="contact">
      <div class="contact__person">
        <div class="contact__name">Tomas Brandt</div>
        <div class="contact__role">Founder &amp; CEO</div>
        <div class="contact__address">Suite # 418, Kell Bldg,<br>NY 40517</div>
      </div>
      <div class="contact__divider"></div>
      <ul class="contact__lines">
        <li>
          <svg class="icon" viewBox="0 0 18 18" aria-hidden="true"><circle cx="9" cy="9" r="9" fill="var(--orange)"/></svg>
          /velvetpress
        </li>
        <li>
          <svg class="icon" viewBox="0 0 18 18" aria-hidden="true"><circle cx="9" cy="9" r="9" fill="var(--orange)"/></svg>
          /velvetpress
        </li>
        <li>
          <svg class="icon" viewBox="0 0 18 18" aria-hidden="true"><circle cx="9" cy="9" r="9" fill="var(--orange)"/></svg>
          /velvetpressings
        </li>
        <li class="gap">
          <svg class="icon" viewBox="0 0 18 18" aria-hidden="true"><circle cx="9" cy="9" r="9" fill="var(--orange)"/><rect x="4.5" y="5.5" width="9" height="7" fill="#fff"/><path d="M4.5 5.5L9 9.5l4.5-4" stroke="var(--orange)" stroke-width="1.2" fill="none"/></svg>
          tomas@velvet-pressings.example
        </li>
        <li>
          <svg class="icon" viewBox="0 0 18 18" aria-hidden="true"><circle cx="9" cy="9" r="9" fill="var(--orange)"/><circle cx="9" cy="9" r="4.8" stroke="#fff" stroke-width="1.3" fill="none"/><path d="M4.2 9h9.6M9 4.2v9.6" stroke="#fff" stroke-width="1.1"/></svg>
          www.velvet-pressings.example
        </li>
      </ul>
    </div>
  </section>
</main>
</body>
</html>
```